Maple Grove Schools | brand new stationery!

We need stationery design with our new logo! Our company updated it's name and image and we like to incorporate the new one on our stationery, business cards and email signature. We are looking for fresh, new ideas!
Industry: Childcare, Elementary and Middle School
Company Name: Maple Grove Schools
Tagline: Bright Futures Start Here
Main colors: Blue, white and a little yellow
Star shape is something new for us! Do you see a way to incorporate it as a design element?

```html
<!DOCTYPE html>
<html lang="en">
<head>
<meta charset="utf-8">
<title>Maple Grove Schools – Stationery</title>
<link href="https://fonts.googleapis.com/css2?family=Poppins:wght@400;500;600&family=Lora:wght@400&display=swap" rel="stylesheet">
<style>
  :root {
    --backdrop: #dadada;
    --paper: #ffffff;
    --navy: #0a1a6e;
    --ink: #1c1c1c;
    --edge: #3a3a3a;
    --ghost: #ececec;
  }
  * { margin: 0; padding: 0; box-sizing: border-box; }
  html, body { width: 1200px; height: 749px; overflow: hidden; }
  body { background: var(--backdrop); position: relative; font-family: "Lora", serif; color: var(--ink); }

  .sheet { position: absolute; background: var(--paper); }

  .brand { position: absolute; text-align: center; font-family: "Poppins", sans-serif; font-weight: 600; color: var(--ink); line-height: 1.05; }
  .brand-dot { display: block; margin: 0 auto 3px; border-radius: 50%; background: var(--navy); }

  .contact-list { list-style: none; position: absolute; }
  .contact-list li { display: flex; align-items: center; gap: 3px; white-space: nowrap; }
  .contact-list svg { flex: none; }

  .address-line { position: absolute; display: flex; align-items: center; white-space: nowrap; }
  .address-line .rule { height: 1px; background: var(--navy); flex: none; }

  .ghost-mark { position: absolute; border-radius: 50%; background: var(--ghost); }

  /* Letterhead */
  .letterhead { left: 388px; top: 133px; width: 371px; height: 479px; border-right: 1px solid var(--edge); border-bottom: 1px solid var(--edge); }
  .letterhead .brand { left: 22px; top: 12px; width: 70px; font-size: 10.5px; }
  .letterhead .brand-dot { width: 18px; height: 18px; }
  .letterhead .contact-list { right: 22px; top: 13px; font-size: 6.6px; line-height: 8.8px; text-align: right; }
  .letterhead .contact-list li { justify-content: flex-end; }
  .letterhead .ghost-mark { left: 135px; top: 220px; width: 110px; height: 110px; }
  .letterhead .address-line { left: 29px; top: 456px; font-size: 8px; gap: 5px; }
  .letterhead .address-line .rule { width: 51px; margin-top: 4px; }

  /* Business card */
  .business-card { left: 161px; top: 335px; width: 347px; height: 105px; box-shadow: 1px 1px 3px rgba(0,0,0,.3); }
  .card-holder { position: absolute; left: 18px; top: 20px; }
  .card-name { font-family: "Poppins", sans-serif; font-weight: 500; font-size: 9px; color: var(--navy); line-height: 11px; }
  .card-role { font-size: 6.8px; line-height: 9px; }
  .business-card .contact-list { left: 18px; top: 45px; font-size: 6.8px; line-height: 9px; }
  .business-card .brand { left: 250px; top: 14px; width: 80px; font-size: 13px; }
  .business-card .brand-dot { width: 20px; height: 20px; }
  .business-card .address-line { left: 18px; top: 86px; font-size: 6.8px; gap: 2px; }
  .business-card .address-line .rule { width: 76px; margin-top: 3px; }

  /* Envelope */
  .envelope-front { left: 800px; top: 231px; width: 295px; height: 148px; border-bottom: 1px solid var(--edge); }
  .envelope-front .brand { left: 12px; top: 11px; width: 52px; font-size: 8.5px; }
  .envelope-front .brand-dot { width: 15px; height: 15px; }
  .envelope-front .ghost-mark { left: 112px; top: 35px; width: 75px; height: 75px; }
  .envelope-front .address-line { left: 23px; top: 130px; font-size: 6.5px; gap: 4px; }
  .envelope-front .address-line .rule { width: 41px; margin-top: 3px; }

  .envelope-back { left: 800px; top: 387px; width: 295px; height: 148px; border-bottom: 1px solid var(--edge); }
  .envelope-flap { position: absolute; left: 0; top: 0; width: 295px; height: 36px; }
</style>
</head>
<body>

<section class="sheet letterhead" aria-label="Letterhead">
  <div class="brand"><span class="brand-dot"></span>Maple Grove<br>Schools</div>
  <ul class="contact-list">
    <li>044-555 010 234
      <svg width="7" height="7" viewBox="0 0 10 10"><rect x=".5" y=".5" width="9" height="9" rx="1" fill="none" stroke="#0a1a6e"/><path d="M3 2.5c0 3 1.5 4.5 4.5 5l.5-1.3-1.4-.7-.6.7C5 5.7 4.3 5 4 4l.7-.6L4 2z" fill="#0a1a6e"/></svg></li>
    <li>hello@maplegrove.org
      <svg width="7" height="7" viewBox="0 0 10 10"><rect x=".5" y="2" width="9" height="6" fill="#0a1a6e"/><path d="M.5 2l4.5 3.5L9.5 2" fill="none" stroke="#fff" stroke-width=".8"/></svg></li>
    <li>www.maplegrove.org
      <svg width="7" height="7" viewBox="0 0 10 10"><circle cx="5" cy="5" r="4.4" fill="none" stroke="#0a1a6e"/><ellipse cx="5" cy="5" rx="1.8" ry="4.4" fill="none" stroke="#0a1a6e" stroke-width=".7"/><path d="M.6 5h8.8M1.3 3h7.4M1.3 7h7.4" stroke="#0a1a6e" stroke-width=".6"/></svg></li>
  </ul>
  <div class="ghost-mark"></div>
  <div class="address-line"><span class="rule"></span>Your Address line goes,here, Country Code 0123456<span class="rule"></span></div>
</section>

<section class="sheet business-card" aria-label="Business card">
  <div class="card-holder">
    <p class="card-name">Clara Bennett</p>
    <p class="card-role">Managing Director</p>
  </div>
  <ul class="contact-list">
    <li><svg width="7" height="7" viewBox="0 0 10 10"><rect x=".5" y=".5" width="9" height="9" rx="1" fill="none" stroke="#0a1a6e"/><path d="M3 2.5c0 3 1.5 4.5 4.5 5l.5-1.3-1.4-.7-.6.7C5 5.7 4.3 5 4 4l.7-.6L4 2z" fill="#0a1a6e"/></svg>044-555 010 234</li>
    <li><svg width="7" height="7" viewBox="0 0 10 10"><rect x=".5" y="2" width="9" height="6" fill="#0a1a6e"/><path d="M.5 2l4.5 3.5L9.5 2" fill="none" stroke="#fff" stroke-width=".8"/></svg>hello@maplegrove.org</li>
    <li><svg width="7" height="7" viewBox="0 0 10 10"><circle cx="5" cy="5" r="4.4" fill="none" stroke="#0a1a6e"/><ellipse cx="5" cy="5" rx="1.8" ry="4.4" fill="none" stroke="#0a1a6e" stroke-width=".7"/><path d="M.6 5h8.8M1.3 3h7.4M1.3 7h7.4" stroke="#0a1a6e" stroke-width=".6"/></svg>www.maplegrove.org</li>
  </ul>
  <div class="brand"><span class="brand-dot"></span>Maple Grove<br>Schools</div>
  <div class="address-line"><span class="rule"></span>Your Address line here, Country Code 0123456<span class="rule"></span></div>
</section>

<section class="sheet envelope-front" aria-label="Envelope front">
  <div class="brand"><span class="brand-dot"></span>Maple Grove<br>Schools</div>
  <div class="ghost-mark"></div>
  <div class="address-line"><span class="rule"></span>Your Address line goes,here, Country Code 0123456<span class="rule"></span></div>
</section>

<section class="sheet envelope-back" aria-label="Envelope back">
  <svg class="envelope-flap" viewBox="0 0 295 36" preserveAspectRatio="none"><polygon points="0,0 295,0 284,35 11,35" fill="var(--navy)"/></svg>
</section>

</body>
</html>
```